Corporate Design für die Vela Serena! GmbH
Zielgruppe
Die Vela Serena! GmbH begibt sich auf den Weg mit den Firmen, die sie gründet, kauft, entwickelt und verkauft. Wir sind eine Holding, beteiligen uns an Firmen oder gründen diese neu. 'Vela Serena!' ist der Pilgergruß auf dem Jakobsweg - diesen bin ich schon 5 Mal gegangen und die Metapher 'Gründen als Weg/Pilgerreise' finde ich sehr zutreffend. Ferner gibt es einen gelben Pfeil auf dem Jakobsweg, der einen immer verfolgt und einem den Weg weist. Das sind wir auch.
Aufgabenstellung
Es ist am Ende das Tages eine Holding, bei der sich Gründer und Firmen melden sollen, weil sie Beratung oder Kapital brauchen - daher ist Seriosität zwar unbedingt notwendig aber sie soll nicht abschrecken, elitär, 'Anwalt-grau-blau-weiß-bieder' sein. Gründertum, Unternehmertum, Freude, Machen, Erfolg!
Pilgern macht Freude und Gründen und Firmen haben auch. Mit uns um so mehr! Ein toller Weg!
'Vela Serena!' eben
Wir heißen 'Vela Serena! GmbH' - mit einem Ausrufezeichen angemeldet und das ist wichtig. Wir haben keine 'Fragezeichen' oder 'Punkte' wir haben ein Ausrufezeichen und einen Pfeil, ein Ziel, einen Weg, Etappen...
Die Abkürzung 'VS!' kann eine Möglichkeit sein aber ausgeschrieben wäre mir lieber - VS! kann das Favicon oder eine Logo-Kurzform/Variante sein

```html
<!DOCTYPE html>
<html lang="de">
<head>
<meta charset="utf-8">
<title>Vela Serena! GmbH – Corporate Design</title>
<link href="https://fonts.googleapis.com/css2?family=Montserrat:wght@400;500;600&display=swap" rel="stylesheet">
<style>
:root{
  --blue:#3a72c9;
  --ink:#333333;
  --paper:#ffffff;
  --window:#cccccc;
  --text:#2b2b2b;
  --shadow:0 4px 14px rgba(0,0,0,.22);
}
*{margin:0;padding:0;box-sizing:border-box}
html,body{width:1200px;height:5108px;overflow:hidden;background:var(--paper)}
body{position:relative;font-family:"Montserrat",sans-serif;color:var(--text)}
.abs{position:absolute}

/* brand lockup */
.brand{position:absolute;display:flex;flex-direction:column;align-items:center}
.brand-dot{border-radius:50%}
.brand-name{font-family:"Montserrat",sans-serif;font-weight:400;white-space:nowrap;line-height:1}
.on-ink .brand-dot{background:var(--ink)} .on-ink .brand-name{color:var(--ink)}
.on-blue .brand-dot{background:var(--blue)} .on-blue .brand-name{color:var(--blue)}
.on-white .brand-dot{background:var(--paper)} .on-white .brand-name{color:var(--paper)}

/* master logos */
.logo-master{left:0;width:1200px}
.logo-master .brand-dot{width:200px;height:200px;margin-bottom:90px}
.logo-master .brand-name{font-size:118px;letter-spacing:6px}

/* letterhead */
.letterhead{left:84px;top:1624px;width:1016px;height:1436px;background:var(--paper);box-shadow:var(--shadow)}
.letterhead .band{left:0;top:0;width:34px;height:100%;background:var(--blue)}
.letterhead .brand{right:48px;top:40px;align-items:center}
.letterhead .brand-dot{width:80px;height:80px;margin-bottom:34px}
.letterhead .brand-name{font-size:34px;letter-spacing:1px}
.window-mark{width:12px;height:12px;border-color:#777;border-style:solid;border-width:0}
.return-line{left:120px;top:226px;font-size:12px;font-weight:500;color:#333}
.contact-list{left:772px;top:222px;list-style:none;font-size:15px;line-height:22px;color:#333}
.contact-list li{display:flex;align-items:center;gap:8px}
.contact-list svg{width:12px;height:12px;fill:#333}
.fold{left:0;width:8px;height:1px;background:#555}
.letter-foot{top:1366px;font-size:14px;line-height:18px;color:#333;border-left:2px solid var(--blue);padding-left:6px}

/* business cards */
.card{width:484px;height:314px;background:var(--paper);box-shadow:var(--shadow);overflow:hidden}
.card .brand-dot{width:60px;height:60px;margin-bottom:22px}
.card .brand-name{font-size:36px;letter-spacing:1px}
.card-front-blue{left:96px;top:3144px;background:var(--blue)}
.card-front-blue .brand{left:0;right:0;top:92px}
.card-back-split{left:630px;top:3144px}
.card-back-split .panel{right:0;top:0;width:244px;height:100%;background:var(--blue)}
.card-back-split .brand{right:0;width:244px;top:22px}
.card-back-split .brand-dot{width:46px;height:46px;margin-bottom:14px}
.card-back-split .brand-name{font-size:25px}
.person{font-size:15px;font-weight:600;color:#333;line-height:16px}
.person small{display:block;font-size:11px;font-weight:400}
.card-addr{font-size:11px;line-height:14px;color:#333}
.card-contacts{list-style:none;font-size:11px;line-height:18px}
.card-contacts li{display:flex;align-items:center;gap:10px}
.card-contacts svg{width:10px;height:10px}
.card-front-white{left:96px;top:3532px}
.card-front-white .band,.card-back-white .band{left:0;top:0;width:26px;height:100%;background:var(--blue)}
.card-front-white .brand{left:26px;right:0;top:90px}
.card-back-white{left:630px;top:3532px}
.card-back-white .brand{right:20px;top:22px}
.card-back-white .brand-dot{width:46px;height:46px;margin-bottom:14px}
.card-back-white .brand-name{font-size:25px}

/* envelopes */
.envelope{left:90px;width:1030px;height:516px;background:var(--paper);box-shadow:var(--shadow);overflow:hidden}
.envelope-front{top:3960px}
.envelope-front .top-line{left:0;top:0;width:100%;height:12px;background:var(--blue)}
.envelope-front .bottom-band{left:0;bottom:0;width:100%;height:14px;background:var(--blue)}
.envelope-front .brand{left:150px;top:96px}
.envelope-front .brand-dot{width:64px;height:64px;margin-bottom:24px}
.envelope-front .brand-name{font-size:32px;letter-spacing:1px}
.address-window{left:90px;top:250px;width:400px;height:200px;border-radius:22px;background:var(--window)}
.envelope-back{top:4546px}
.envelope-back .flap{left:0;top:0;width:100%;height:130px}
.envelope-back .brand{left:0;right:0;top:18px}
.envelope-back .brand-dot{width:56px;height:56px;margin-bottom:20px}
.envelope-back .brand-name{font-size:30px;letter-spacing:1px}
.envelope-back .bottom-band{left:0;bottom:0;width:100%;height:14px;background:var(--blue)}
</style>
</head>
<body>

<!-- master logo, dark -->
<div class="brand logo-master on-ink" style="top:110px">
  <span class="brand-dot"></span>
  <span class="brand-name">VELA SERENA!</span>
</div>

<!-- master logo, blue -->
<div class="brand logo-master on-blue" style="top:876px">
  <span class="brand-dot"></span>
  <span class="brand-name">VELA SERENA!</span>
</div>

<!-- letterhead -->
<section class="abs letterhead" aria-label="Briefbogen">
  <div class="abs band"></div>
  <div class="brand on-blue">
    <span class="brand-dot"></span>
    <span class="brand-name">VELA SERENA!</span>
  </div>

  <span class="abs window-mark" style="left:106px;top:212px;border-top-width:1px;border-left-width:1px"></span>
  <span class="abs window-mark" style="left:510px;top:212px;border-top-width:1px;border-right-width:1px"></span>
  <span class="abs window-mark" style="left:106px;top:420px;border-bottom-width:1px;border-left-width:1px"></span>
  <span class="abs window-mark" style="left:510px;top:420px;border-bottom-width:1px;border-right-width:1px"></span>
  <p class="abs return-line">Vela Serena! GmbH | Musterstrasse 123 | 12345 Musterstadt</p>

  <ul class="abs contact-list">
    <li><svg viewBox="0 0 12 12"><path d="M2 1l2 0 1 3-1.5 1a6 6 0 003 3L8 6.5l3 1v2c0 .8-.7 1.5-1.5 1.5A9.5 9.5 0 01.5 2.5C.5 1.7 1.2 1 2 1z"/></svg>+41 123 / 45 67 89 01</li>
    <li><svg viewBox="0 0 12 12"><rect x="3" y="1" width="6" height="4"/><rect x="1" y="5" width="10" height="5" rx="1"/></svg>+41 123 / 45 67 89 01</li>
    <li><svg viewBox="0 0 12 12"><path d="M0 2h12v8H0z M1 3l5 4 5-4" fill="#333"/><path d="M1 3l5 4 5-4" stroke="#fff" fill="none"/></svg>info@vela-serena.de</li>
    <li><svg viewBox="0 0 12 12"><circle cx="6" cy="6" r="5.5"/><path d="M.5 6h11M6 .5v11" stroke="#fff"/></svg>www.vela-serena.de</li>
  </ul>

  <span class="abs fold" style="top:502px;left:0"></span>
  <span class="abs fold" style="top:1012px;left:0"></span>

  <p class="abs letter-foot" style="left:96px">Musterstrasse 123<br>12345 Musterstadt<br>Geschäftsführung Max Muster</p>
  <p class="abs letter-foot" style="left:382px">Bankverbindung<br>BIC:&nbsp; ABCDEFGHXXX<br>IBAN: DE 00 0000 0000 0000 0000 00</p>
  <p class="abs letter-foot" style="left:764px">Finanzamt<br>Musterstadt<br>USt-IdNr.: DE000000000</p>
</section>

<!-- business card front, blue -->
<section class="abs card card-front-blue" aria-label="Visitenkarte Vorderseite blau">
  <div class="brand on-white">
    <span class="brand-dot"></span>
    <span class="brand-name">VELA SERENA!</span>
  </div>
</section>

<!-- business card back, split -->
<section class="abs card card-back-split" aria-label="Visitenkarte Rückseite">
  <div class="abs panel"></div>
  <div class="brand on-white">
    <span class="brand-dot"></span>
    <span class="brand-name">VELA SERENA!</span>
  </div>
  <p class="abs person" style="left:12px;top:168px">MAX MUSTER<small>Patentanwalt</small></p>
  <p class="abs card-addr" style="left:12px;top:272px">Musterstrasse 123<br>12345 Musterstadt</p>
  <ul class="abs card-contacts" style="left:256px;top:208px;color:#fff">
    <li><svg viewBox="0 0 12 12" fill="#fff"><circle cx="6" cy="6" r="5"/></svg>+41 123 / 45 67 89 01</li>
    <li><svg viewBox="0 0 12 12" fill="#fff"><rect x="1" y="4" width="10" height="6"/></svg>+41 123 / 45 67 89 01</li>
    <li><svg viewBox="0 0 12 12" fill="#fff"><rect x="4" y="0" width="4" height="12" rx="1"/></svg>+41 123 / 45 67 89 01</li>
    <li><svg viewBox="0 0 12 12" fill="#fff"><rect x="0" y="2" width="12" height="8"/></svg>info@vela-serena.de</li>
    <li><svg viewBox="0 0 12 12" fill="#fff"><circle cx="6" cy="6" r="5.5"/></svg>www.vela-serena.de</li>
  </ul>
</section>

<!-- business card front, white -->
<section class="abs card card-front-white" aria-label="Visitenkarte Vorderseite weiß">
  <div class="abs band"></div>
  <div class="brand on-blue">
    <span class="brand-dot"></span>
    <span class="brand-name">VELA SERENA!</span>
  </div>
</section>

<!-- business card back, white -->
<section class="abs card card-back-white" aria-label="Visitenkarte Rückseite weiß">
  <div class="abs band"></div>
  <div class="brand on-blue">
    <span class="brand-dot"></span>
    <span class="brand-name">VELA SERENA!</span>
  </div>
  <p class="abs person" style="left:46px;top:168px">MAX MUSTER<small>Patentanwalt</small></p>
  <p class="abs card-addr" style="left:46px;top:272px">Musterstrasse 123<br>12345 Musterstadt</p>
  <ul class="abs card-contacts" style="left:300px;top:208px;color:#333">
    <li><svg viewBox="0 0 12 12" fill="#333"><circle cx="6" cy="6" r="5"/></svg>+41 123 / 45 67 89 01</li>
    <li><svg viewBox="0 0 12 12" fill="#333"><rect x="1" y="4" width="10" height="6"/></svg>+41 123 / 45 67 89 01</li>
    <li><svg viewBox="0 0 12 12" fill="#333"><rect x="4" y="0" width="4" height="12" rx="1"/></svg>+41 123 / 45 67 89 01</li>
    <li><svg viewBox="0 0 12 12" fill="#333"><rect x="0" y="2" width="12" height="8"/></svg>info@vela-serena.de</li>
    <li><svg viewBox="0 0 12 12" fill="#333"><circle cx="6" cy="6" r="5.5"/></svg>www.vela-serena.de</li>
  </ul>
</section>

<!-- envelope front -->
<section class="abs envelope envelope-front" aria-label="Briefumschlag Vorderseite">
  <div class="abs top-line"></div>
  <div class="brand on-blue">
    <span class="brand-dot"></span>
    <span class="brand-name">VELA SERENA!</span>
  </div>
  <div class="abs address-window"></div>
  <div class="abs bottom-band"></div>
</section>

<!-- envelope back -->
<section class="abs envelope envelope-back" aria-label="Briefumschlag Rückseite">
  <svg class="abs flap" viewBox="0 0 1030 130" preserveAspectRatio="none">
    <path d="M0 0H1030L990 118Q986 130 972 130H58Q44 130 40 118Z" fill="var(--blue)"/>
  </svg>
  <div class="brand on-white">
    <span class="brand-dot"></span>
    <span class="brand-name">VELA SERENA!</span>
  </div>
  <div class="abs bottom-band"></div>
</section>

</body>
</html>
```